Velundra Jobs portal

Velundra Jobs is a job portal connecting job seekers and companies offering part time jobs in the Mena region, starting in the UAE. We would like to see designs that use the color blue. We have attached images to give an idea what the website should look like. When a company posts a job the job seekers are not allowed to see which company has posted a job. There should also be a coinvex gateway. On the landing page we want a catching picture that we will send.

Target Market(s)

Students and promotional workers

Logo Text

Velundra Jobs

Coding

Coded - Design and coding required

Number of Pages Required

4 page

Font styles to use
Sans Serif

Colors
33a6d7
0692cd
85cae6

```html
<!DOCTYPE html>
<html lang="en">
<head>
<meta charset="utf-8">
<title>Velundra Jobs</title>
<link href="https://fonts.googleapis.com/css2?family=Open+Sans:wght@400;600&display=swap" rel="stylesheet">
<style>
:root{
  --teal:#4fc1c6;
  --teal-dark:#3fb0b4;
  --teal-text:#3cbfc7;
  --pink:#e4478a;
  --pink-soft:#fdeef4;
  --pink-frame:#f5c8dc;
  --blue:#3467b5;
  --ink:#444a52;
  --muted:#5d636b;
  --header-bg:#f7f7f8;
  --row-bg:#fdfafb;
  --line:#e6e6e8;
}
*{box-sizing:border-box;margin:0;padding:0}
html,body{width:1200px;height:959px;overflow:hidden;background:#fff;font-family:"Open Sans",Arial,sans-serif;color:var(--ink)}
.page{position:relative;width:1200px;height:959px}
.abs{position:absolute}
.header{left:0;top:0;width:1200px;height:116px;background:var(--header-bg);border-bottom:1px solid var(--line)}
.brand{left:110px;top:42px;font-size:40px;font-weight:400;color:var(--teal);letter-spacing:-0.5px;line-height:1}
.nav a{position:absolute;top:63px;font-size:14px;color:var(--ink);text-decoration:none;letter-spacing:.2px}
.round{width:57px;height:57px;border-radius:50%;background:#e6e6e8;display:flex;align-items:center;justify-content:center;top:40px}
.badge{position:absolute;top:3px;right:15px;font-size:11px;color:var(--pink)}
.avatar{left:887px;top:40px;width:58px;height:58px;border-radius:50%;background:linear-gradient(135deg,#c9a58a,#6d7a86);border:2px solid #fff}
.logout{left:970px;top:59px;width:94px;height:32px;background:var(--teal);color:#fff;font-size:14px;display:flex;align-items:center;justify-content:center}
.categories{left:99px;top:147px;width:158px;height:367px;background:var(--pink);list-style:none;padding-top:13px}
.categories li{display:flex;align-items:center;height:34.3px;color:#fff;font-size:14px;padding-left:8px}
.categories li svg{margin-right:10px}
.categories .count{margin-left:auto;margin-right:10px}
.divider{left:293px;top:132px;width:1px;height:442px;background:var(--line)}
.filter{left:329px;top:145px;width:772px;height:85px;background:var(--pink-soft)}
.field{top:21px;width:203px;height:42px;background:#fff;border:1px solid #eadfe4;font-size:14px;color:var(--muted);padding-left:16px;display:flex;align-items:center}
.filter-btn{left:535px;top:21px;width:203px;height:42px;background:var(--teal);display:flex;color:#fff;font-size:14px}
.filter-btn .icon{width:54px;background:var(--teal-dark);display:flex;align-items:center;justify-content:center}
.filter-btn .label{flex:1;display:flex;align-items:center;justify-content:center}
.col-head{top:256px;font-size:15.5px;color:var(--teal-text)}
.row{left:329px;width:772px;background:var(--row-bg);font-size:14.5px;color:var(--muted)}
.row.active{background:var(--blue);color:#fff}
.row span{position:absolute;top:50%;transform:translateY(-50%)}
.apply{position:absolute;left:617px;top:50%;transform:translateY(-50%);width:126px;height:32px;background:var(--teal);color:#fff;font-size:14.5px;display:flex;align-items:center;justify-content:center}
.featured-title{left:357px;top:613px;font-size:15.5px;color:var(--teal-text)}
.provider{top:677px;width:126px;height:131px;border:3px solid var(--pink-frame)}
.mascot{left:99px;top:600px;width:184px;height:244px;border-radius:50% 50% 45% 45%;background:radial-gradient(ellipse at center,#ececec 0%,#f6f6f6 60%,#fff 100%)}
.footer{top:902px;font-size:13px;color:var(--ink)}
.footer-links{right:100px;top:902px;font-size:13px;color:var(--ink);word-spacing:2px}
</style>
</head>
<body>
<div class="page">
  <header class="abs header">
    <div class="abs brand">velundra</div>
    <nav class="nav">
      <a style="left:438px">ABOUT US</a>
      <a style="left:558px">CONTACT US</a>
    </nav>
    <div class="abs round" style="left:733px">
      <svg width="20" height="20" viewBox="0 0 20 20"><circle cx="8" cy="8" r="6" fill="none" stroke="#444" stroke-width="2.5"/><line x1="12.5" y1="12.5" x2="18" y2="18" stroke="#444" stroke-width="3" stroke-linecap="round"/></svg>
    </div>
    <div class="abs round" style="left:811px">
      <span class="badge">23</span>
      <svg width="20" height="22" viewBox="0 0 20 22"><path d="M10 2c-3.5 0-5.5 2.6-5.5 6v4.5L2.5 16h15l-2-3.5V8c0-3.4-2-6-5.5-6z" fill="none" stroke="#444" stroke-width="1.6" stroke-linejoin="round"/><path d="M8 18.5a2 2 0 0 0 4 0" fill="none" stroke="#444" stroke-width="1.6"/></svg>
    </div>
    <div class="abs avatar" role="img" aria-label="User profile photo"></div>
    <div class="abs logout">LOG OUT</div>
  </header>

  <ul class="abs categories">
    <li><svg width="12" height="12" viewBox="0 0 12 12"><circle cx="6" cy="6" r="4.3" fill="#fff"/><circle cx="6" cy="6" r="1.6" fill="#e4478a"/><g stroke="#fff" stroke-width="2.2"><line x1="6" y1="0" x2="6" y2="12"/><line x1="0" y1="6" x2="12" y2="6"/><line x1="1.8" y1="1.8" x2="10.2" y2="10.2"/><line x1="10.2" y1="1.8" x2="1.8" y2="10.2"/></g><circle cx="6" cy="6" r="1.6" fill="#e4478a"/></svg>Category 1<span class="count">(33)</span></li>
    <li><svg width="12" height="12" viewBox="0 0 12 12"><circle cx="6" cy="6" r="4.3" fill="#fff"/><g stroke="#fff" stroke-width="2.2"><line x1="6" y1="0" x2="6" y2="12"/><line x1="0" y1="6" x2="12" y2="6"/><line x1="1.8" y1="1.8" x2="10.2" y2="10.2"/><line x1="10.2" y1="1.8" x2="1.8" y2="10.2"/></g><circle cx="6" cy="6" r="1.6" fill="#e4478a"/></svg>Category 2<span class="count" style="margin-right:20px">(3)</span></li>
    <li><svg width="12" height="12" viewBox="0 0 12 12"><circle cx="6" cy="6" r="4.3" fill="#fff"/><g stroke="#fff" stroke-width="2.2"><line x1="6" y1="0" x2="6" y2="12"/><line x1="0" y1="6" x2="12" y2="6"/><line x1="1.8" y1="1.8" x2="10.2" y2="10.2"/><line x1="10.2" y1="1.8" x2="1.8" y2="10.2"/></g><circle cx="6" cy="6" r="1.6" fill="#e4478a"/></svg>Category 3<span class="count">(23)</span></li>
    <li><svg width="12" height="12" viewBox="0 0 12 12"><circle cx="6" cy="6" r="4.3" fill="#fff"/><g stroke="#fff" stroke-width="2.2"><line x1="6" y1="0" x2="6" y2="12"/><line x1="0" y1="6" x2="12" y2="6"/><line x1="1.8" y1="1.8" x2="10.2" y2="10.2"/><line x1="10.2" y1="1.8" x2="1.8" y2="10.2"/></g><circle cx="6" cy="6" r="1.6" fill="#e4478a"/></svg>Category 4<span class="count">(33)</span></li>
    <li><svg width="12" height="12" viewBox="0 0 12 12"><circle cx="6" cy="6" r="4.3" fill="#fff"/><g stroke="#fff" stroke-width="2.2"><line x1="6" y1="0" x2="6" y2="12"/><line x1="0" y1="6" x2="12" y2="6"/><line x1="1.8" y1="1.8" x2="10.2" y2="10.2"/><line x1="10.2" y1="1.8" x2="1.8" y2="10.2"/></g><circle cx="6" cy="6" r="1.6" fill="#e4478a"/></svg>Category 5<span class="count">(13)</span></li>
    <li><svg width="12" height="12" viewBox="0 0 12 12"><circle cx="6" cy="6" r="4.3" fill="#fff"/><g stroke="#fff" stroke-width="2.2"><line x1="6" y1="0" x2="6" y2="12"/><line x1="0" y1="6" x2="12" y2="6"/><line x1="1.8" y1="1.8" x2="10.2" y2="10.2"/><line x1="10.2" y1="1.8" x2="1.8" y2="10.2"/></g><circle cx="6" cy="6" r="1.6" fill="#e4478a"/></svg>Category 6<span class="count">(18)</span></li>
    <li><svg width="12" height="12" viewBox="0 0 12 12"><circle cx="6" cy="6" r="4.3" fill="#fff"/><g stroke="#fff" stroke-width="2.2"><line x1="6" y1="0" x2="6" y2="12"/><line x1="0" y1="6" x2="12" y2="6"/><line x1="1.8" y1="1.8" x2="10.2" y2="10.2"/><line x1="10.2" y1="1.8" x2="1.8" y2="10.2"/></g><circle cx="6" cy="6" r="1.6" fill="#e4478a"/></svg>Category 7<span class="count">(33)</span></li>
    <li><svg width="12" height="12" viewBox="0 0 12 12"><circle cx="6" cy="6" r="4.3" fill="#fff"/><g stroke="#fff" stroke-width="2.2"><line x1="6" y1="0" x2="6" y2="12"/><line x1="0" y1="6" x2="12" y2="6"/><line x1="1.8" y1="1.8" x2="10.2" y2="10.2"/><line x1="10.2" y1="1.8" x2="1.8" y2="10.2"/></g><circle cx="6" cy="6" r="1.6" fill="#e4478a"/></svg>Category 8<span class="count">(43)</span></li>
    <li><svg width="12" height="12" viewBox="0 0 12 12"><circle cx="6" cy="6" r="4.3" fill="#fff"/><g stroke="#fff" stroke-width="2.2"><line x1="6" y1="0" x2="6" y2="12"/><line x1="0" y1="6" x2="12" y2="6"/><line x1="1.8" y1="1.8" x2="10.2" y2="10.2"/><line x1="10.2" y1="1.8" x2="1.8" y2="10.2"/></g><circle cx="6" cy="6" r="1.6" fill="#e4478a"/></svg>Category 9<span class="count">(23)</span></li>
    <li><svg width="12" height="12" viewBox="0 0 12 12"><circle cx="6" cy="6" r="4.3" fill="#fff"/><g stroke="#fff" stroke-width="2.2"><line x1="6" y1="0" x2="6" y2="12"/><line x1="0" y1="6" x2="12" y2="6"/><line x1="1.8" y1="1.8" x2="10.2" y2="10.2"/><line x1="10.2" y1="1.8" x2="1.8" y2="10.2"/></g><circle cx="6" cy="6" r="1.6" fill="#e4478a"/></svg>Category 9<span class="count">(22)</span></li>
  </ul>

  <div class="abs divider"></div>
  <div class="abs mascot" role="img" aria-label="Faint mascot character illustration"></div>

  <section class="abs filter">
    <div class="abs field" style="left:38px">Type a Keyword</div>
    <div class="abs field" style="left:286px">District 1</div>
    <div class="abs filter-btn">
      <div class="icon"><svg width="22" height="22" viewBox="0 0 22 22"><circle cx="9" cy="9" r="7" fill="none" stroke="#fff" stroke-width="2.5"/><line x1="14" y1="14" x2="20" y2="20" stroke="#fff" stroke-width="3" stroke-linecap="round"/><line x1="9" y1="5.5" x2="9" y2="12.5" stroke="#fff" stroke-width="2"/><line x1="5.5" y1="9" x2="12.5" y2="9" stroke="#fff" stroke-width="2"/></svg></div>
      <div class="label">Filter Jobs</div>
    </div>
  </section>

  <div class="abs col-head" style="left:373px">Job Title</div>
  <div class="abs col-head" style="left:566px">Due Date</div>
  <div class="abs col-head" style="left:802px">Provider Name</div>

  <div class="abs row active" style="top:299px;height:57px">
    <span style="left:28px">Job Title Number 1</span><span style="left:236px">Due Date: 23 jan 2105</span><span style="left:474px">Provider 1</span>
    <div class="apply" style="left:617px">Apply Now</div>
  </div>
  <div class="abs row" style="top:369px;height:56px">
    <span style="left:28px">Job Title Number 2</span><span style="left:237px">Due Date: 23 jan 2105</span><span style="left:475px">Provider 1</span>
    <div class="apply" style="left:618px">Apply Now</div>
  </div>
  <div class="abs row" style="top:437px;height:56px">
    <span style="left:28px">Job Title Number 3</span><span style="left:237px">Due Date: 23 jan 2105</span><span style="left:475px">Provider 1</span>
    <div class="apply" style="left:618px">Apply Now</div>
  </div>
  <div class="abs row" style="top:506px;height:56px">
    <span style="left:28px">Job Title Number 4</span><span style="left:237px">Due Date: 23 jan 2105</span><span style="left:475px">Provider 1</span>
    <div class="apply" style="left:618px">Apply Now</div>
  </div>

  <h2 class="abs featured-title" style="font-weight:400">Featured Job Providers</h2>
  <div class="abs provider" style="left:358px;background:#9dd8d6" role="img" aria-label="Illustration of a job seeker holding a job wanted sign"></div>
  <div class="abs provider" style="left:513px;background:linear-gradient(135deg,#5a5a5a,#9a9a9a)" role="img" aria-label="Photo of a hand with a magnifying glass over candidate icons"></div>
  <div class="abs provider" style="left:667px;background:linear-gradient(180deg,#dfe3e0,#b0a898)" role="img" aria-label="Photo of a businessman with binoculars on a beach"></div>
  <div class="abs provider" style="left:821px;background:linear-gradient(180deg,#8ec6f0,#c6e2f7)" role="img" aria-label="Photo of a businessman climbing stairs toward the sky"></div>
  <div class="abs provider" style="left:975px;background:linear-gradient(180deg,#b9d7ef,#3a3a44)" role="img" aria-label="Illustration of two historical gentlemen"></div>

  <footer>
    <div class="abs footer" style="left:99px">Copyright © Velundra. All Rights Reserved.</div>
    <div class="abs footer-links">About Us &nbsp;/&nbsp; Terms and Condition &nbsp;/&nbsp; Sitemap</div>
  </footer>
</div>
</body>
</html>
```